Business card por a urban DJ, up scale audience target

Need a sober design, modern, conservative colors but i can consider some options, y play rnb, hip hop, EDM and top40.

Business card for contact and personal info, double sided, use logo attrached please; im 42 so i need a card acording to my age an target audience.

Target Market(s)

Adult people, up scale audience

Industry/Entity Type

Music Download

Contact Information for Business Card

Cel (318) 4207265518 www.lumadrift.com

Requirements
Must have
• open mind
Nice to have
• open mind
Should not have
• DJ

```html
<!DOCTYPE html>
<html lang="en">
<head>
<meta charset="utf-8">
<title>Luma Business Card</title>
<link rel="stylesheet" href="https://fonts.googleapis.com/css2?family=Montserrat:wght@400;600&display=swap">
<style>
  :root {
    --stage: #e6e6e6;
    --card-light: #ffffff;
    --card-shade: #d9d9d9;
    --ink: #1c1c1c;
    --ink-soft: #8a8a8a;
    --band-dark: #262626;
    --band-mid: #5a5a5a;
  }
  * { margin: 0; padding: 0; box-sizing: border-box; }
  html, body {
    width: 1200px; height: 950px; overflow: hidden;
    background: var(--stage);
    font-family: "Montserrat", Arial, sans-serif;
  }
  .card {
    position: absolute; left: 250px;
    width: 700px; height: 400px;
    overflow: hidden;
    background: linear-gradient(135deg, var(--card-light) 45%, var(--card-shade) 100%);
    box-shadow: 0 8px 24px rgba(0,0,0,.18);
  }
  .card--back { top: 55px; }
  .card--front { top: 495px; background: linear-gradient(200deg, var(--card-shade) 0%, var(--card-light) 55%); }
  .card__band { position: absolute; inset: 0; width: 700px; height: 400px; }
  .wordmark {
    position: absolute;
    font-weight: 600; color: var(--ink); letter-spacing: 2px; line-height: 1;
    white-space: nowrap;
  }
  .card--back .wordmark { left: 230px; top: 125px; font-size: 104px; }
  .card--back .site-url {
    position: absolute; left: 300px; top: 255px;
    font-size: 18px; letter-spacing: 4px; color: var(--ink-soft); font-weight: 600;
  }
  .card--front .wordmark { right: 70px; top: 118px; font-size: 88px; }
  .contact { position: absolute; left: 60px; top: 150px; }
  .contact__name { font-size: 22px; font-weight: 600; color: var(--ink); letter-spacing: 1px; }
  .contact__role { font-size: 15px; color: var(--ink-soft); letter-spacing: 1px; margin-top: 2px; }
  .contact__line {
    display: flex; align-items: center; gap: 10px;
    font-size: 17px; color: #333; margin-top: 10px;
  }
  .contact__role + .contact__line { margin-top: 14px; }
  .contact__line svg { width: 16px; height: 16px; flex: none; }
</style>
</head>
<body>
  <section class="card card--back">
    <svg class="card__band" viewBox="0 0 700 400" aria-hidden="true">
      <polygon points="0,250 250,400 0,400" fill="var(--band-dark)"/>
    </svg>
    <p class="wordmark">LUMA</p>
    <p class="site-url">LUMADRIFT.COM</p>
  </section>

  <section class="card card--front">
    <svg class="card__band" viewBox="0 0 700 400" aria-hidden="true">
      <polygon points="380,400 700,300 700,400" fill="var(--band-mid)"/>
      <polygon points="470,400 700,330 700,400" fill="var(--band-dark)"/>
    </svg>
    <p class="wordmark">LUMA</p>
    <div class="contact">
      <p class="contact__name">MARCO DELL</p>
      <p class="contact__role">PRESIDENT</p>
      <p class="contact__line">
        <svg viewBox="0 0 16 16" aria-hidden="true"><rect x="4" y="1" width="8" height="14" rx="1.5" fill="none" stroke="var(--ink)" stroke-width="1.6"/><circle cx="8" cy="12.3" r="0.9" fill="var(--ink)"/></svg>
        (318) 4207265518
      </p>
      <p class="contact__line">
        <svg viewBox="0 0 16 16" aria-hidden="true"><circle cx="8" cy="8" r="6.5" fill="none" stroke="var(--ink)" stroke-width="1.6"/><path d="M1.5 8h13M8 1.5c-3 3.5-3 9.5 0 13M8 1.5c3 3.5 3 9.5 0 13" fill="none" stroke="var(--ink)" stroke-width="1.2"/></svg>
        www.lumadrift.com
      </p>
    </div>
  </section>
</body>
</html>
```